Presentation Folder, for Cancer Awareness, VERY COLORFULL AND MODERN

This will be a standard size folder that will hold standard 8 1/2 x 11 papers with a business card slot on the flap, this is a very easy project with very little text and the design for the back page is already done so all you really have to do is make a very nice colorful front cover, you will see my attachments are labeled and I gave you alot of instructions, this should be a very fast easy project
Updates

Reason: there has not been enough quality designs, sorry

Target Market(s)

Our Target Market is Dr's that Deal with Cancer patients

Industry/Entity Type

Healthcare

Font styles to use
Serif

Colors

Designer to choose colors to be used in the design.

Requirements
Must have
• Project must be tasteful and look professional with the ribbons as the main focal point in the center of folder the folder should be a nice gray color to accent the color of the ribbons , the back page needs no design it is the" Sorvane Test" in the attachments I sent
Nice to have
• I would like the ribbons displayed in a row, I included a logo sample layout
• a picture on the front of the folder under the words Hereditary Cancer Screening - Then under that put the words - The Power of Knowledge - then add the picture I labeled Great Picture in the attachments

```html
<!DOCTYPE html>
<html lang="en">
<head>
<meta charset="utf-8">
<title>Hereditary Cancer Screening Presentation Folder – Inside Spread</title>
<link rel="stylesheet" href="https://fonts.googleapis.com/css2?family=Open+Sans:wght@400;600&display=swap">
<style>
  :root {
    --backdrop: #2e2e2e;
    --sheet: #ffffff;
    --panel-grey: #efefef;
    --trim-blue: #7fd3ec;
    --fold-blue: #9fb8c4;
    --bleed-green: #3cc47a;
    --sheet-top-red: #e06a6a;
    --slot-red: #e0303a;
    --ink: #1f1f1f;
    --accent-pink: #f27f8e;
  }
  html, body {
    margin: 0;
    padding: 0;
    width: 1200px;
    height: 835px;
    overflow: hidden;
    background: var(--backdrop);
  }
  .folder-spread {
    position: absolute;
    left: 17px;
    top: 43px;
    width: 1166px;
    height: 749px;
    display: block;
  }
  .sheet { fill: var(--sheet); }
  .sheet-top-edge { stroke: var(--sheet-top-red); stroke-width: 1.5; }
  .panel { fill: var(--panel-grey); stroke: var(--trim-blue); stroke-width: 1; }
  .fold-line { stroke: var(--fold-blue); stroke-width: 1; stroke-dasharray: 3 3; }
  .bleed-line { stroke: var(--bleed-green); stroke-width: 1; stroke-dasharray: 4 3; }
  .pocket { stroke: var(--trim-blue); stroke-width: 1; }
  .card-slot-mark { stroke: var(--slot-red); stroke-width: 1; }
  .pocket-copy {
    font-family: "Open Sans", sans-serif;
    font-size: 15px;
    fill: var(--ink);
  }
  .pocket-copy .highlight { fill: var(--accent-pink); font-weight: 600; }
</style>
</head>
<body>
<svg class="folder-spread" viewBox="0 0 1214 780" xmlns="http://www.w3.org/2000/svg">
  <defs>
    <linearGradient id="ribbon-row-left" x1="0" x2="1" y1="0" y2="0">
      <stop offset="0" stop-color="#f2b6cc"/>
      <stop offset="0.28" stop-color="#b9dcd8"/>
      <stop offset="0.5" stop-color="#f2cfc4"/>
      <stop offset="0.72" stop-color="#cfc8ee"/>
      <stop offset="1" stop-color="#b8b4f2"/>
    </linearGradient>
    <linearGradient id="ribbon-row-right" x1="0" x2="1" y1="0" y2="0">
      <stop offset="0" stop-color="#d9bfe8"/>
      <stop offset="0.28" stop-color="#c9c9c9"/>
      <stop offset="0.5" stop-color="#bfe6e6"/>
      <stop offset="0.72" stop-color="#ece7bf"/>
      <stop offset="1" stop-color="#c7c7de"/>
    </linearGradient>
    <linearGradient id="pocket-left-fill" x1="0" x2="1" y1="0" y2="0">
      <stop offset="0" stop-color="#eaeaea"/>
      <stop offset="0.3" stop-color="#f4f4f4"/>
      <stop offset="0.55" stop-color="#ffffff"/>
      <stop offset="1" stop-color="#ececec"/>
    </linearGradient>
    <linearGradient id="pocket-right-fill" x1="0" x2="1" y1="0" y2="0">
      <stop offset="0" stop-color="#ececec"/>
      <stop offset="0.5" stop-color="#ffffff"/>
      <stop offset="1" stop-color="#ececec"/>
    </linearGradient>
  </defs>

  <!-- Flat sheet -->
  <rect class="sheet" x="0" y="0" width="1214" height="780"/>
  <line class="sheet-top-edge" x1="0" y1="0.75" x2="1214" y2="0.75"/>

  <!-- Inside panels -->
  <rect class="panel" x="22" y="21" width="564" height="717"/>
  <rect class="panel" x="627" y="21" width="564" height="717"/>

  <!-- Awareness ribbon rows -->
  <rect x="70" y="137" width="516" height="323" rx="60" fill="url(#ribbon-row-left)" opacity="0.55"
        role="img" aria-label="Row of overlapping awareness ribbons in pink, teal, peach, lavender and violet"/>
  <rect x="627" y="137" width="518" height="323" rx="60" fill="url(#ribbon-row-right)" opacity="0.55"
        role="img" aria-label="Row of overlapping awareness ribbons in lilac, grey, aqua, pale yellow and slate"/>

  <!-- Fold and bleed guides -->
  <line class="fold-line" x1="606" y1="0" x2="606" y2="780"/>
  <line class="bleed-line" x1="0" y1="758" x2="1214" y2="758"/>

  <!-- Left pocket with business card slot -->
  <path class="pocket" fill="url(#pocket-left-fill)"
        d="M56 780 L56 538 L500 538 Q536 538 541 590 L573 780 Z"/>
  <g class="card-slot-marks">
    <line class="card-slot-mark" x1="188" y1="632" x2="226" y2="592"/>
    <line class="card-slot-mark" x1="378" y1="592" x2="416" y2="632"/>
    <line class="card-slot-mark" x1="188" y1="686" x2="226" y2="726"/>
    <line class="card-slot-mark" x1="378" y1="726" x2="416" y2="686"/>
  </g>

  <!-- Right pocket with copy -->
  <path class="pocket" fill="url(#pocket-right-fill)"
        d="M640 780 L672 590 Q677 538 713 538 L1157 538 L1157 780 Z"/>
  <text class="pocket-copy" text-anchor="middle">
    <tspan x="910" y="610">At our state of the art, <tspan class="highlight">CLIA certified</tspan> and <tspan class="highlight">ACCREDA</tspan></tspan>
    <tspan x="910" y="631">accredited facility we perform Next Generation Sequencing</tspan>
    <tspan x="910" y="652"><tspan class="highlight">(NGS)</tspan> based screening for mutations known to</tspan>
    <tspan x="910" y="674">affect an individual's Risk of developing Hereditary Cancer.</tspan>
    <tspan x="910" y="695">Results from the test enable the Physician to make Better</tspan>
    <tspan x="910" y="717">informed treatment decisions.</tspan>
  </text>
</svg>
</body>
</html>
```